Moxy Fen needs some awesome stationary

Do you have what it takes to get my brand? You either do or you don't, have a crack at a design and you my just win my business.

I don't want to waste your or my time, so put your creative genius on either a business card or envelope.

I however need a package of stationary that follows the same brand. I will message you to complete the remaining should I like your first submission.

Here is what I need, have a go!

Basically I need the following for my small business based in melbourne.
- Letterhead (printer ready and MS Word)
- Business Card
- Compliments Slip
- Envelope
- Proposal Cover Page (MS Word only)
- Presentation Folder
- Marbled Fox Cards
- Student Name Tent
- Index Cards
- Vell-Ka

I am establishing the brand and it must be modern, professional but also relaxed; that is not formal and not corporate. It represents a company are leaders, but small enough to care and operate like a bunch of friends. We are bringing people and conversations back to business, and turfing out all the bureaucracy and crazy and wasteful procedures. Its about "lets talk and figure it out together and find even better ways".

Target Market(s)

Mainly companies that build software products, but Agile practices are used in many other industries (even graphic design projects)

Industry/Entity Type

Information Technology

Font styles to use
Sans Serif

Colors
3176b5
aaaaaa

Requirements
Must have
• I like curves and circles and not boxes or rectangles.
• I want a colour rich design with my brand colours, but it must be balanced.
• I want more modern than traditional, but simple modern
Should not have
• Not corporate
• Please don't waste my time if your not going to think about it.
• Don't mess with my primary logo
• Don't change my colours
• Don't overlay logo on image

```html
<!DOCTYPE html>
<html lang="en">
<head>
<meta charset="utf-8">
<title>Moxy Fen Stationery</title>
<link rel="stylesheet" href="https://fonts.googleapis.com/css2?family=Open+Sans:wght@400;600;700&display=swap">
<style>
  :root {
    --stage: #2e9be0;
    --brand: #2a55a6;
    --brand-deep: #244b95;
    --grey: #aaaaaa;
    --paper: #ffffff;
    --paper-shade: #f1f3f6;
    --ink: #2b2b2b;
  }
  * { box-sizing: border-box; margin: 0; padding: 0; }
  html, body { width: 1200px; height: 977px; overflow: hidden; }
  body {
    background: var(--stage);
    font-family: "Open Sans", Arial, sans-serif;
    color: var(--ink);
    position: relative;
  }
  .sheet {
    position: absolute;
    background: var(--paper);
    box-shadow: 0 6px 14px rgba(0, 30, 80, 0.25);
  }
  .brand-mark {
    display: flex;
    align-items: center;
    gap: 6px;
    color: var(--brand);
    font-weight: 600;
    white-space: nowrap;
  }
  .brand-mark .dot {
    border-radius: 50%;
    background: var(--brand);
    flex: none;
  }
  .brand-mark.sm { font-size: 12px; }
  .brand-mark.sm .dot { width: 16px; height: 16px; }
  .brand-mark.md { font-size: 15px; }
  .brand-mark.md .dot { width: 22px; height: 22px; }

  .contact { font-size: 6px; line-height: 1.55; color: #555; }
  .contact .company { font-size: 8px; font-weight: 700; color: var(--brand); margin-bottom: 2px; }
  .contact .row { display: flex; align-items: center; gap: 3px; }
  .contact .row::before {
    content: ""; width: 5px; height: 5px; border-radius: 50%;
    background: var(--brand); flex: none;
  }

  /* Card stacks */
  .card-stack { width: 74px; height: 40px; display: flex; align-items: center; justify-content: center; border-bottom: 4px solid #e3e6eb; }
  .card-stack.one { left: 210px; top: 145px; }
  .card-stack.two { left: 310px; top: 165px; }
  .card-stack .brand-mark { font-size: 9px; gap: 4px; }
  .card-stack .brand-mark .dot { width: 12px; height: 12px; }

  /* DL envelope front */
  .envelope-front { left: 130px; top: 195px; width: 295px; height: 170px; border-bottom: 3px solid var(--brand); border-left: 3px solid var(--brand); }
  .envelope-front .brand-mark { position: absolute; left: 14px; top: 16px; }
  .envelope-front .contact { position: absolute; left: 14px; bottom: 14px; }

  /* Envelope back */
  .envelope-back { left: 60px; top: 370px; width: 315px; height: 215px; background: var(--paper-shade); overflow: hidden; }
  .envelope-back svg { position: absolute; left: 0; top: 0; }
  .envelope-back .brand-mark { position: absolute; left: 50%; top: 140px; transform: translateX(-50%); }

  /* Letterhead */
  .letterhead { left: 400px; top: 195px; width: 355px; height: 470px; padding: 22px 26px; }
  .letterhead .head { display: flex; justify-content: space-between; align-items: flex-start; }
  .letterhead .abn { font-size: 5.5px; color: #777; margin-top: 3px; margin-left: 28px; }
  .letterhead .body { margin-top: 26px; font-size: 6.6px; line-height: 1.55; color: #333; }
  .letterhead .body p { margin-bottom: 10px; }

  /* Folder */
  .folder { left: 760px; top: 225px; width: 360px; height: 500px; background: var(--brand); color: #fff; display: flex; flex-direction: column; align-items: center; justify-content: center; }
  .folder .texture { position: absolute; inset: 0; background: linear-gradient(160deg, #2d5aad, #264f9c); }
  .folder .brand-mark { position: relative; color: #fff; font-size: 32px; gap: 12px; }
  .folder .brand-mark .dot { width: 40px; height: 40px; background: #fff; }
  .folder .legal { position: relative; font-size: 15px; font-weight: 700; margin-top: 6px; }

  /* Compliments slip */
  .comp-slip { left: 345px; top: 685px; width: 320px; height: 170px; border-left: 3px solid var(--brand); border-bottom: 3px solid var(--brand); }
  .comp-slip .brand-mark { position: absolute; left: 14px; top: 16px; }
  .comp-slip .contact { position: absolute; left: 14px; top: 88px; }
  .comp-slip .with { position: absolute; right: 14px; bottom: 10px; font-size: 6px; color: var(--brand); }

  /* Business cards */
  .card-front { left: 680px; top: 760px; width: 170px; height: 102px; background: var(--brand); display: flex; flex-direction: column; align-items: center; justify-content: center; }
  .card-front .brand-mark { color: #fff; font-size: 13px; }
  .card-front .brand-mark .dot { width: 18px; height: 18px; background: #fff; }
  .card-front .web { color: #dfe8f7; font-size: 6.5px; margin-top: 4px; }

  .card-back { left: 865px; top: 770px; width: 170px; height: 102px; padding: 12px; display: flex; gap: 10px; }
  .card-back .side { display: flex; flex-direction: column; gap: 3px; padding-top: 8px; }
  .card-back .side .brand-mark { font-size: 9px; gap: 4px; }
  .card-back .side .brand-mark .dot { width: 12px; height: 12px; }
  .card-back .side .legal { font-size: 6px; font-weight: 700; color: var(--brand); }
  .card-back .person { font-size: 7px; font-weight: 700; color: var(--brand); letter-spacing: 0.5px; text-transform: uppercase; }
  .card-back .role { font-size: 4.5px; color: #777; margin-bottom: 3px; }
  .card-back .contact { font-size: 5px; }
</style>
</head>
<body>

  <div class="sheet card-stack one"><div class="brand-mark"><span class="dot"></span>Moxy Fen</div></div>
  <div class="sheet card-stack two"><div class="brand-mark"><span class="dot"></span>Moxy Fen</div></div>

  <div class="sheet envelope-front">
    <div class="brand-mark md"><span class="dot"></span>Moxy Fen</div>
    <div class="contact">
      <div class="company">Moxy Fen Pty Ltd</div>
      <div class="row">PO Box 4417, Brindle Vale, VIC 3190, Australia</div>
      <div class="row">1300 555 019</div>
      <div class="row">hello@moxyfen.example</div>
      <div class="row">www.moxyfen.example</div>
    </div>
  </div>

  <div class="sheet envelope-back">
    <svg width="315" height="215" viewBox="0 0 315 215" aria-hidden="true">
      <rect x="0" y="0" width="315" height="30" fill="var(--brand)"/>
      <polygon points="0,30 315,30 290,110 25,110" fill="#dcdfe4"/>
      <polygon points="0,30 25,110 0,215" fill="#e8ebef"/>
      <polygon points="315,30 290,110 315,215" fill="#e8ebef"/>
    </svg>
    <div class="brand-mark md"><span class="dot"></span>Moxy Fen</div>
  </div>

  <div class="sheet letterhead">
    <div class="head">
      <div>
        <div class="brand-mark md"><span class="dot"></span>Moxy Fen</div>
        <div class="abn">ABN No. 12 345 678 901</div>
      </div>
      <div class="contact">
        <div class="company">Moxy Fen Pty Ltd</div>
        <div class="row">PO Box 4417, Brindle Vale, VIC 3190</div>
        <div class="row">1300 555 019</div>
        <div class="row">hello@moxyfen.example</div>
        <div class="row">www.moxyfen.example</div>
      </div>
    </div>
    <div class="body">
      <p>Thanks for taking the time to talk with us last week. We enjoyed hearing how your team works and where the friction sits today. This letter sums up what we heard and the ideas we shared together.</p>
      <p>Our proposal is simple. We run a short series of open sessions with your people, map the work as it really flows, and remove steps that add no value. Nothing is fixed in advance; we learn as we go and adjust with you.</p>
      <p>If this sounds right, reply to this letter or call us and we will set a first meeting. We look forward to figuring it out together.</p>
    </div>
  </div>

  <div class="sheet folder">
    <div class="texture" role="img" aria-label="Subtle tone-on-tone repeating brand pattern across the folder cover"></div>
    <div class="brand-mark"><span class="dot"></span>Moxy Fen</div>
    <div class="legal">Moxy Fen Pty Ltd</div>
  </div>

  <div class="sheet comp-slip">
    <div class="brand-mark md"><span class="dot"></span>Moxy Fen</div>
    <div class="contact">
      <div class="company">Moxy Fen Pty Ltd</div>
      <div class="row">PO Box 4417, Brindle Vale, VIC 3190, Australia</div>
      <div class="row">1300 555 019</div>
      <div class="row">hello@moxyfen.example</div>
      <div class="row">www.moxyfen.example</div>
    </div>
    <div class="with">With Compliments</div>
  </div>

  <div class="sheet card-front">
    <div class="brand-mark"><span class="dot"></span>Moxy Fen</div>
    <div class="web">www.moxyfen.example</div>
  </div>

  <div class="sheet card-back">
    <div class="side">
      <div class="brand-mark"><span class="dot"></span>Moxy Fen</div>
      <div class="legal">Moxy Fen Pty Ltd</div>
    </div>
    <div>
      <div class="person">Jonah Pell</div>
      <div class="role">Agile Coach &amp; Trainer</div>
      <div class="contact">
        <div class="row">PO Box 4417, Brindle Vale, VIC 3190</div>
        <div class="row">1300 555 019</div>
        <div class="row">+61 400 555 019</div>
        <div class="row">jonah@moxyfen.example</div>
      </div>
    </div>
  </div>

</body>
</html>
```